Local Flower Farm Needs Business Card Design

I need business cards designed for a flower farm based in Eudora, Kansas.
Business Info:
We are a local cut flower farm located in Eudora, Kansas, founded by Corinne Haldwick. What started as a passion for agriculture and search for more joy in daily life has blossomed into a small business dedicated to providing the community with beautiful, fresh, and sustainable flowers. We specialize in local, seasonal blooms, ensuring that every petal reflects the care and dedication we pour into our craft. Our mission is to deliver the highest quality flowers directly to our customers through local farmers markets and to florists who share our commitment to sustainability. Join us in celebrating the beauty of nature, one bloom at a time!
Contact Details:
Corinne Haldwick
Owner
Phone 913-555-0147
Facebook: Rosalind Thorpe Gardens
Instagram: @RosalindThorpeGardens
Website: RosalindThorpeGardens.example
Target Market(s)
Wholesale to Florists and Direct to Consumer via Farmers Market
Industry/Entity Type
Florist, Farm
Contact Information for Business Card
Name, Contact Info, Logo
Look and feel
Each slider illustrates characteristics of the customer's brand and the style your logo design should communicate.

```html
<!DOCTYPE html>
<html lang="en">
<head>
<meta charset="utf-8">
<title>Rosalind Thorpe Gardens — Business Card</title>
<link rel="stylesheet" href="https://fonts.googleapis.com/css2?family=Montserrat:wght@400;500;700&display=swap">
<style>
  :root {
    --page-bg: #e4e6e5;
    --card-light: #f1f1f1;
    --card-dark: #08222a;
    --ink-dark: #0b2229;
    --ink-light: #e6e8e7;
    --rule-light: rgba(230, 232, 231, 0.75);
    --rule-dark: rgba(11, 34, 41, 0.7);
  }
  * { box-sizing: border-box; margin: 0; padding: 0; }
  html, body {
    width: 1200px;
    height: 1200px;
    overflow: hidden;
    background: var(--page-bg);
    font-family: "Montserrat", sans-serif;
  }
  .sheet {
    position: relative;
    width: 1200px;
    height: 1200px;
  }
  .card {
    position: absolute;
    left: 220px;
    width: 760px;
    height: 434px;
    border-radius: 4px;
    box-shadow: 0 10px 28px rgba(0, 0, 0, 0.18);
  }
  .card--front {
    top: 141px;
    background: var(--card-light);
    color: var(--ink-dark);
  }
  .card--back {
    top: 625px;
    background: var(--card-dark);
    color: var(--ink-light);
  }
  .holder {
    position: absolute;
    left: 69px;
    top: 62px;
  }
  .holder__name {
    font-weight: 700;
    font-size: 25px;
    letter-spacing: 0.2px;
    line-height: 1.2;
  }
  .holder__role {
    font-weight: 400;
    font-size: 19px;
    line-height: 1.3;
  }
  .contact {
    position: absolute;
    left: 69px;
    top: 290px;
    font-weight: 400;
    font-size: 19px;
    line-height: 1.36;
  }
  .contact__phone { margin-bottom: 6px; }
  .brand-seal {
    position: absolute;
    border-radius: 50%;
    display: flex;
    align-items: center;
    justify-content: center;
    text-align: center;
    font-weight: 500;
    text-transform: uppercase;
  }
  .brand-seal--small {
    left: 541px;
    top: 217px;
    width: 150px;
    height: 150px;
    border: 1px solid var(--rule-dark);
    color: var(--ink-dark);
    font-size: 13px;
    letter-spacing: 1.6px;
    line-height: 1.5;
  }
  .brand-seal--large {
    left: 276px;
    top: 113px;
    width: 208px;
    height: 208px;
    border: 1px solid var(--rule-light);
    color: var(--ink-light);
    font-size: 18px;
    letter-spacing: 2.2px;
    line-height: 1.5;
  }
  .social {
    position: absolute;
    left: 55px;
    top: 370px;
    display: flex;
    align-items: center;
    gap: 10px;
    font-weight: 400;
    font-size: 19px;
    letter-spacing: 0.3px;
  }
  .social__dot {
    width: 22px;
    height: 22px;
    border-radius: 50%;
    background: var(--ink-light);
  }
</style>
</head>
<body>
  <main class="sheet">
    <section class="card card--front" aria-label="Business card front">
      <div class="holder">
        <p class="holder__name">Corinne Haldwick</p>
        <p class="holder__role">Owner</p>
      </div>
      <div class="contact">
        <p class="contact__phone">913-555-0147</p>
        <p class="contact__email">corinne@<br>rosalindthorpegardens.example</p>
      </div>
      <div class="brand-seal brand-seal--small">Rosalind<br>Thorpe<br>Gardens</div>
    </section>

    <section class="card card--back" aria-label="Business card back">
      <div class="brand-seal brand-seal--large">Rosalind<br>Thorpe<br>Gardens</div>
      <div class="social">
        <span class="social__dot"></span>
        <span class="social__handle">@RosalindThorpeGardens</span>
      </div>
    </section>
  </main>
</body>
</html>
```